Verlindo Magician

I want the business card for my business to give to people who watch that later I will be employed to show magic here is my website http://www.balsamomagicien.com/I want the interesting design , i am very opened for formal and informal, I watch a lot of design so don't stick to the common shape and form but i hope it can also be produced the thing to write on will be the same as in picture that i will upload , i also will upload the logo for you that so can be easy to useDenis CostilleMagicianMAGICIAN BALSAMO 17 rue des Tilleuls - 25000 BESANÇON contact@verlindoillusions.example tel. 0381 946 157 tel. 0674 219 503

```html
<!DOCTYPE html>
<html lang="fr">
<head>
<meta charset="utf-8">
<title>Verlindo Magician – Business Card</title>
<link href="https://fonts.googleapis.com/css2?family=Jost:wght@300;400&display=swap" rel="stylesheet">
<style>
  :root {
    --bg: #3b3b3b;
    --red: #e8242a;
    --ink: #111111;
    --grey: #555555;
    --rule: #a8a8a8;
    --paper: #ffffff;
  }
  * { margin: 0; padding: 0; box-sizing: border-box; }
  html, body { width: 1200px; height: 960px; overflow: hidden; }
  body {
    background: var(--bg);
    font-family: "Jost", "Futura", sans-serif;
    font-weight: 300;
    position: relative;
  }
  .card {
    position: absolute;
    width: 600px;
    height: 342px;
    overflow: hidden;
    box-shadow: 0 10px 30px rgba(0,0,0,.45);
  }
  /* Front */
  .card--front { left: 60px; top: 80px; background: var(--red); }
  .front__portrait {
    position: absolute;
    left: 225px; top: 70px;
    width: 150px; height: 150px;
    border-radius: 40% 40% 18% 18%;
    background: radial-gradient(circle at 50% 35%, #3a3a3a, var(--ink) 70%);
  }
  .front__url {
    position: absolute;
    left: 0; right: 0; top: 268px;
    text-align: center;
    color: var(--paper);
    font-size: 15px;
    letter-spacing: 2px;
  }
  /* Back */
  .card--back { left: 540px; top: 520px; background: var(--paper); }
  .back__portrait {
    position: absolute;
    left: 440px; top: 26px;
    width: 110px; height: 110px;
    border-radius: 40% 40% 18% 18%;
    background: radial-gradient(circle at 50% 35%, #3a3a3a, var(--ink) 70%);
  }
  .back__brand {
    position: absolute;
    right: 34px; top: 142px;
    display: flex; align-items: center; gap: 8px;
    font-size: 26px;
    letter-spacing: 1px;
    color: var(--ink);
  }
  .back__brand-dot { width: 8px; height: 8px; border-radius: 50%; background: var(--red); }
  .back__rule {
    position: absolute;
    left: 40px; right: 40px; top: 236px;
    border-top: 1px solid var(--rule);
  }
  .person { position: absolute; left: 40px; top: 178px; }
  .person__name { font-size: 30px; font-weight: 400; color: var(--ink); line-height: 1; }
  .person__role { font-size: 19px; color: var(--red); line-height: 1.2; }
  .contacts {
    position: absolute; left: 40px; top: 248px;
    list-style: none;
    font-size: 16px; color: var(--grey);
  }
  .contacts li { display: flex; align-items: center; gap: 10px; height: 22px; }
  .contacts svg { width: 14px; height: 14px; fill: var(--ink); }
  .studio {
    position: absolute; right: 40px; top: 248px;
    text-align: right;
    font-size: 15px; color: var(--grey); line-height: 21px;
  }
  .studio__name { color: var(--red); font-size: 16px; }
  .studio__url { letter-spacing: 1.5px; }
  .band--black {
    position: absolute; left: 0; bottom: 0;
    width: 62%; height: 10px; background: var(--ink);
  }
  .band--red {
    position: absolute; right: 0; bottom: 0;
    width: 38%; height: 16px; background: var(--red);
  }
</style>
</head>
<body>

<section class="card card--front">
  <div class="front__portrait" role="img" aria-label="Black and white illustration of the magician holding a playing card"></div>
  <p class="front__url">www.verlindoillusions.example</p>
</section>

<section class="card card--back">
  <div class="back__portrait" role="img" aria-label="Black and white illustration of the magician holding a playing card"></div>
  <div class="back__brand"><span class="back__brand-dot"></span>VERLINDO</div>

  <div class="person">
    <p class="person__name">Marc Ravoulet</p>
    <p class="person__role">Magician</p>
  </div>

  <div class="back__rule"></div>

  <ul class="contacts">
    <li>
      <svg viewBox="0 0 24 24"><path d="M6.6 10.8a15 15 0 0 0 6.6 6.6l2.2-2.2c.3-.3.7-.4 1-.2 1.1.4 2.3.6 3.6.6.6 0 1 .4 1 1V20c0 .6-.4 1-1 1A17 17 0 0 1 3 4c0-.6.4-1 1-1h3.5c.6 0 1 .4 1 1 0 1.3.2 2.5.6 3.6.1.3 0 .7-.2 1z"/></svg>
      0381 946 157
    </li>
    <li>
      <svg viewBox="0 0 24 24"><path d="M6.6 10.8a15 15 0 0 0 6.6 6.6l2.2-2.2c.3-.3.7-.4 1-.2 1.1.4 2.3.6 3.6.6.6 0 1 .4 1 1V20c0 .6-.4 1-1 1A17 17 0 0 1 3 4c0-.6.4-1 1-1h3.5c.6 0 1 .4 1 1 0 1.3.2 2.5.6 3.6.1.3 0 .7-.2 1z"/></svg>
      0674 219 503
    </li>
    <li>
      <svg viewBox="0 0 24 24"><path d="M2 5h20v14H2z M4 7v.5l8 5.5 8-5.5V7l-8 5.5z" fill-rule="evenodd"/></svg>
      contact@verlindoillusions.example
    </li>
  </ul>

  <div class="studio">
    <p class="studio__name">MAGICIAN VERLINDO</p>
    <p class="studio__address">17 rue des Tilleuls - 25000 BESANÇON</p>
    <p class="studio__url">www.verlindoillusions.example</p>
  </div>

  <div class="band--black"></div>
  <div class="band--red"></div>
</section>

</body>
</html>
```